Corvane Business Cards

Front of business card will have logo, name, address, & telephone number. Back of card will have a list of services provided - Roads, Substation Pads, Temporary Pads, Site Pads, Land Leveling, Powerline Row Cleaning, Land Clearing, Gates, Fencing, Construction Entrances, Excavation, Trenching, Underground Utilities, Directional Boring, Pile Driving. We are a construction company that uses heavy equipment like bulldozers, motor graders/blades, dump trucks, backhoes, hydro axes, & skid loaders. We build roads, pads, & install electric utility lines & waterlines underground. This logo is new. The word "Construction" can be smaller as uploaded 2 example edited logos. We will be using this card design for many employees.
Target Market(s)
Industrial Electric Powerline, Wind Turbine, Solar Panel, & Water Utility companies.
Contact Information for Business Card
Name/Position - Dwayne Halster - Owner
Address: 4875 FM 309
Ashgrove, KS 66412
Phone number - (555) 482-5096

```html
<!DOCTYPE html>
<html lang="en">
<head>
<meta charset="utf-8">
<title>Corvane Construction Business Cards</title>
<link rel="stylesheet" href="https://fonts.googleapis.com/css2?family=Arimo:wght@400;700&display=swap">
<style>
  :root {
    --maroon: #3b1119;
    --maroon-line: #8a5a63;
    --paper: #ffffff;
    --ink: #2b2b2b;
    --muted: #555555;
    --backdrop: #4a4a4a;
  }
  * { margin: 0; padding: 0; box-sizing: border-box; }
  html, body {
    width: 1200px;
    height: 1015px;
    overflow: hidden;
    background: var(--backdrop);
    font-family: "Arimo", Arial, sans-serif;
  }
  .canvas {
    position: relative;
    width: 1200px;
    height: 1015px;
  }
  .card {
    position: absolute;
    left: 280px;
    width: 640px;
    height: 366px;
    box-shadow: 0 10px 24px rgba(0,0,0,0.35);
  }
  .card-back {
    top: 90px;
    background: var(--maroon);
    color: var(--paper);
    display: flex;
    flex-direction: column;
    align-items: center;
    justify-content: center;
    text-align: center;
    padding: 0 40px;
  }
  .service-list, .company-about, .company-work {
    font-size: 17px;
    line-height: 1.32;
  }
  .divider {
    width: 150px;
    height: 1px;
    background: var(--maroon-line);
    margin: 16px 0;
  }
  .card-front {
    top: 540px;
    background: var(--paper);
    display: flex;
    align-items: center;
  }
  .brand {
    width: 340px;
    align-self: stretch;
    display: flex;
    flex-direction: column;
    align-items: center;
    justify-content: center;
    gap: 14px;
    padding-top: 60px;
    color: var(--maroon);
  }
  .brand-mark {
    width: 44px;
    height: 44px;
    background: var(--maroon);
  }
  .brand-name {
    font-size: 28px;
    font-weight: 700;
    letter-spacing: 2px;
    text-align: center;
    line-height: 1.15;
  }
  .rule {
    width: 1px;
    height: 170px;
    background: var(--muted);
  }
  .contact {
    padding-left: 30px;
    padding-right: 20px;
    color: var(--ink);
  }
  .contact-name {
    font-size: 24px;
    font-weight: 700;
    color: var(--maroon);
    text-transform: uppercase;
    line-height: 1;
    white-space: nowrap;
  }
  .contact-role {
    font-size: 16px;
    color: var(--muted);
    margin: 2px 0 0 20px;
  }
  .contact-phone {
    font-size: 18px;
    font-weight: 700;
    color: var(--maroon);
    margin: 16px 0 0 44px;
    white-space: nowrap;
  }
  .contact-phone span { margin-left: 4px; }
  .contact-address {
    font-style: normal;
    font-size: 16px;
    color: var(--muted);
    line-height: 1.3;
    margin: 16px 0 0 66px;
    white-space: nowrap;
  }
</style>
</head>
<body>
<main class="canvas">
  <section class="card card-back" aria-label="Card back: services">
    <p class="service-list">Roads, Substation Pads | Temporary Pads | Site Pads,<br>
      Land Leveling | Powerline Row Cleaning | Land Clearing<br>
      Gates | Fencing,Construction Entrances | Excavation<br>
      Trenching | Underground Utilities | Directional Boring | Pile Driving.</p>
    <div class="divider"></div>
    <p class="company-about">We are a construction company that uses heavy equipment<br>
      like bulldozers | motor graders/blades | dump trucks<br>
      backhoes | hydro axes &amp; skid loaders.</p>
    <div class="divider"></div>
    <p class="company-work">We build roads, pads<br>
      install electric utility lines &amp; waterlines underground.</p>
  </section>

  <section class="card card-front" aria-label="Card front: contact">
    <div class="brand">
      <div class="brand-mark"></div>
      <p class="brand-name">CORVANE<br>CONSTRUCTION</p>
    </div>
    <div class="rule"></div>
    <div class="contact">
      <h1 class="contact-name">Dwayne Halster</h1>
      <p class="contact-role">Owner</p>
      <p class="contact-phone">P:<span>(555) 482-5096</span></p>
      <address class="contact-address">4875 FM 309<br>Ashgrove, KS 66412</address>
    </div>
  </section>
</main>
</body>
</html>
```